Business Card Design

Attached is my current Business card I do not like it but I must save the logo portion of it. Don't like the color or the lettering am looking for more architectural look in grays or taupe with the green more of a charturese color and the blue a charcoal color on a textured paper that looks more like something high-end that would appeal to an architect or a designer. We make concrete decorative items such as concrete fireplaces, sinks, tops and more.

Target Market(s)

Architects designers of Commercial and Residential - artistic features

Industry/Entity Type

Architect

Contact Information for Business Card

Marisol T. Quenby President and Marketing Director
602-418-5093
email marisol@vantorelstone.example
Showroom "Quillmont Design Center" 4183 W Palomar Scottsdale AZ
Fax: 602-731-6624

Font styles to use
Sans Serif

Requirements
Must have
• Architectural
Natural and earthy colors with a touch of color in the existing attached

```html
<!DOCTYPE html>
<html lang="en">
<head>
<meta charset="utf-8">
<title>Vantorel Stone Design Studio – Business Card</title>
<link rel="stylesheet" href="https://fonts.googleapis.com/css2?family=Exo+2:wght@300;400&display=swap">
<style>
  :root {
    --stage: #e6e5e2;
    --slate: #6a6d70;
    --slate-grain: #63666a;
    --paper: #ececec;
    --chartreuse: #7fb536;
    --charcoal-text: #5c5f62;
    --white: #ffffff;
    --shadow: rgba(0, 0, 0, 0.18);
  }
  * { box-sizing: border-box; margin: 0; padding: 0; }
  html, body {
    width: 1200px;
    height: 1000px;
    overflow: hidden;
    background: var(--stage);
    font-family: "Exo 2", sans-serif;
  }
  .sheet {
    width: 1200px;
    height: 1000px;
    display: flex;
    flex-direction: column;
    align-items: center;
    justify-content: center;
    gap: 60px;
  }
  .card {
    position: relative;
    width: 700px;
    height: 400px;
    overflow: hidden;
    box-shadow: 0 10px 28px var(--shadow);
    background:
      repeating-linear-gradient(90deg, var(--slate) 0 3px, var(--slate-grain) 3px 4px);
  }
  .studio-band {
    position: absolute;
    right: 0;
    bottom: 0;
    height: 42px;
    background: var(--chartreuse);
    color: var(--white);
    font-weight: 300;
    font-size: 18px;
    letter-spacing: 0.3px;
    display: flex;
    align-items: center;
    justify-content: flex-end;
    padding-right: 28px;
  }
  .wordmark {
    display: flex;
    align-items: center;
    gap: 10px;
    font-weight: 300;
    font-size: 34px;
    line-height: 1;
  }
  .wordmark-square {
    width: 18px;
    height: 18px;
    background: var(--chartreuse);
  }

  /* Front */
  .card-front .studio-band { left: 0; }
  .card-front .brand {
    position: absolute;
    left: 210px;
    top: 140px;
    color: var(--white);
  }
  .card-front .tagline {
    margin-top: 16px;
    font-weight: 300;
    font-size: 17px;
    color: #e4e5e6;
  }

  /* Back */
  .card-back .contact-panel {
    position: absolute;
    left: 0;
    top: 0;
    bottom: 0;
    width: 300px;
    background: var(--paper);
    padding: 56px 0 0 46px;
  }
  .card-back .wordmark { color: var(--charcoal-text); font-size: 28px; }
  .contact-list {
    list-style: none;
    margin-top: 98px;
    font-size: 14.5px;
    font-weight: 400;
    color: var(--charcoal-text);
    line-height: 1.45;
  }
  .contact-list li {
    display: flex;
    align-items: flex-start;
    gap: 9px;
  }
  .contact-list svg { flex: none; margin-top: 4px; fill: var(--chartreuse); }
  .contact-list .showroom { color: var(--chartreuse); }
  .contact-list .address { padding-left: 21px; }
  .card-back .identity {
    position: absolute;
    right: 36px;
    top: 100px;
    text-align: right;
    color: var(--white);
  }
  .card-back .person-name {
    font-weight: 300;
    font-size: 38px;
    letter-spacing: 0.5px;
  }
  .card-back .person-title {
    font-weight: 300;
    font-size: 15px;
    color: #e4e5e6;
    margin-top: 2px;
  }
  .card-back .studio-band { left: 270px; }
</style>
</head>
<body>
<main class="sheet">

  <section class="card card-front" aria-label="Card front">
    <div class="brand">
      <div class="wordmark"><span class="wordmark-square"></span>Vantorel Stone</div>
      <p class="tagline">Put our experience to work for you</p>
    </div>
    <div class="studio-band">Vantorel Stone Design Studio</div>
  </section>

  <section class="card card-back" aria-label="Card back">
    <div class="contact-panel">
      <div class="wordmark"><span class="wordmark-square"></span>Vantorel Stone</div>
      <ul class="contact-list">
        <li>
          <svg width="12" height="12" viewBox="0 0 24 24" aria-hidden="true"><path d="M6.6 10.8a15.1 15.1 0 0 0 6.6 6.6l2.2-2.2a1 1 0 0 1 1-.25 11.4 11.4 0 0 0 3.6.57 1 1 0 0 1 1 1V20a1 1 0 0 1-1 1A17 17 0 0 1 3 4a1 1 0 0 1 1-1h3.5a1 1 0 0 1 1 1c0 1.25.2 2.45.57 3.57a1 1 0 0 1-.25 1z"/></svg>
          602-418-5093
        </li>
        <li>
          <svg width="12" height="12" viewBox="0 0 24 24" aria-hidden="true"><path d="M6 2h9v5H6zM3 9h18a1 1 0 0 1 1 1v9a1 1 0 0 1-1 1H3a1 1 0 0 1-1-1v-9a1 1 0 0 1 1-1zm3 3v2h6v-2z"/></svg>
          602-731-6624
        </li>
        <li>
          <svg width="12" height="12" viewBox="0 0 24 24" aria-hidden="true"><path d="M2 5h20v14H2zm2 2v.5l8 5 8-5V7z"/></svg>
          marisol@vantorelstone.example
        </li>
        <li class="showroom">
          <svg width="12" height="12" viewBox="0 0 24 24" aria-hidden="true"><path d="M12 3l10 9h-3v9h-5v-6h-4v6H5v-9H2z"/></svg>
          Vantorel Stone Showroom
        </li>
        <li class="address">"Quillmont Design Center" 4183 W<br>Palomar Scottsdale AZ</li>
      </ul>
    </div>
    <div class="identity">
      <h1 class="person-name">Marisol T. Quenby</h1>
      <p class="person-title">President &amp; Marketing Director</p>
    </div>
    <div class="studio-band">Vantorel Stone Design Studio</div>
  </section>

</main>
</body>
</html>
```